Northvale Strategy Partners Website Design

I need a website design for my new business consulting and executive coaching firm, Northvale Strategy Partners. We provide consultative services to business C-suites as well as personal coaching to executives. I have attached the logo with color scheme I have chosen. I would like the website to reflect professionalism and continue the color scheme in the logo.

Target Market(s)

Small to medium business and their executives; middle to upper income men and women in mid- to late career looking for significance

Industry/Entity Type

Business Consultant

Number of Pages Required

4 page

Requirements
Must have
• A homepage with prominent logo and way to contact for more information; an area on the homepage with easy to read, clear text to describe what the company does; a prominent area on the homepage for a tagline; a blog page that can be updated regularly, an "about us" page with biographical information; an "about us" page; a page detailing services offered
• The web design must match the logo colors and font that I have uploaded.
Nice to have
• A lighthouse picture in the background or header
Should not have
• A lot of text area on the homepage

```html
<!DOCTYPE html>
<html lang="en">
<head>
<meta charset="utf-8">
<title>Northvale Strategy Partners</title>
<link href="https://fonts.googleapis.com/css2?family=Asap:wght@400;500;600&family=Open+Sans:wght@400;600&display=swap" rel="stylesheet">
<style>
:root{
  --navy:#1f2d5c;
  --red:#6e1014;
  --ink:#4a4a4a;
  --muted:#8c8c8c;
  --soft:#f1f1f1;
  --band:#e9e9e9;
  --line:#e2e2e2;
  --white:#ffffff;
}
*{margin:0;padding:0;box-sizing:border-box}
html,body{width:705px;height:1200px;overflow:hidden;background:var(--white)}
body{font-family:"Open Sans",Arial,sans-serif;color:var(--ink);position:relative}
.abs{position:absolute}
.header{position:absolute;left:0;top:0;width:705px;height:72px;background:var(--white)}
.nav-link{position:absolute;top:32px;font-family:"Asap",Arial,sans-serif;font-size:9px;color:#555;letter-spacing:.2px;white-space:nowrap}
.nav-link.active{color:var(--navy)}
.nav-link.active::after{content:"";position:absolute;left:-4px;right:-4px;top:18px;height:2px;background:var(--red)}
.brand{position:absolute;left:314px;top:26px;width:76px;text-align:center;font-family:"Asap",Arial,sans-serif;font-weight:600;color:var(--navy);white-space:nowrap}
.brand-name{display:block;font-size:10.5px;line-height:12px;letter-spacing:.6px}
.brand-sub{display:block;font-size:5px;line-height:7px;letter-spacing:.4px;border-top:1px solid var(--navy);margin-top:1px}
.search{position:absolute;left:588px;top:22px;width:31px;height:28px;background:var(--navy);color:var(--white);font-size:5px;text-align:center;font-family:"Asap",Arial,sans-serif}
.search svg{display:block;margin:6px auto 2px}
.hero{position:absolute;left:0;top:72px;width:705px;height:258px;background:linear-gradient(180deg,#2c3a78 0%,#5d63a8 38%,#c99bc4 70%,#8e7aa8 86%,#3c4e78 100%)}
.hero-title{position:absolute;left:0;top:206px;width:705px;text-align:center;font-family:"Asap",Arial,sans-serif;font-size:19px;color:var(--white);letter-spacing:.5px}
.section-title{position:absolute;left:0;width:705px;text-align:center;font-family:"Asap",Arial,sans-serif;font-size:17px;font-weight:400;color:#555}
.offer-name{position:absolute;width:180px;text-align:center;font-family:"Asap",Arial,sans-serif;font-size:8.5px;font-weight:500;color:var(--navy);top:508px}
.offer-text{position:absolute;width:180px;text-align:center;font-size:6px;line-height:11px;color:var(--muted);top:531px}
.provide{position:absolute;left:0;top:594px;width:705px;height:316px;background:var(--soft)}
.provide-text{position:absolute;top:838px;width:245px;font-size:6px;line-height:11px;color:var(--muted)}
.newsletter{position:absolute;left:0;top:910px;width:705px;height:63px;background:var(--band)}
.news-label{position:absolute;left:125px;top:935px;font-family:"Asap",Arial,sans-serif;font-size:8.5px;color:#333}
.email-field{position:absolute;left:222px;top:928px;width:301px;height:26px;background:var(--white);border:1px solid #ddd;font-size:5px;color:#aaa;padding:10px 0 0 9px}
.subscribe{position:absolute;left:527px;top:928px;width:92px;height:26px;background:var(--red);color:var(--white);font-family:"Asap",Arial,sans-serif;font-size:8.5px;text-align:center;line-height:26px}
.footer-rule{position:absolute;left:0;width:705px;height:1px;background:var(--line)}
.footer-brand{position:absolute;left:318px;top:990px;width:69px;height:34px;background:var(--white);text-align:center;font-family:"Asap",Arial,sans-serif;font-weight:600;color:var(--navy);padding-top:10px;white-space:nowrap}
.footer-brand .brand-name{font-size:8.5px;line-height:10px;letter-spacing:.5px}
.footer-brand .brand-sub{font-size:4px;line-height:6px;letter-spacing:.3px}
.col-head{position:absolute;top:1047px;font-family:"Asap",Arial,sans-serif;font-weight:600;font-size:6.5px;color:var(--navy)}
.col-head::after{content:"";position:absolute;left:0;top:13px;height:1px;background:var(--line)}
.h1::after{width:68px}.h2::after{width:122px}.h3::after{width:124px}.h4::after{width:124px}
.quick{position:absolute;left:85px;top:1070px;font-size:5.5px;line-height:14px;color:#555;list-style:none}
.small{position:absolute;font-size:5.5px;line-height:10px;color:#555}
.date{color:var(--red)}
.ico{position:absolute;left:452px}
.copy{position:absolute;top:1178px;font-size:5.5px;color:#555}
</style>
</head>
<body>

<header class="header">
  <span class="nav-link active" style="left:131px">HOME</span>
  <span class="nav-link" style="left:175px">ABOUT US</span>
  <span class="nav-link" style="left:233px">SERVICES</span>
  <div class="brand"><span class="brand-name">NORTHVALE</span><span class="brand-sub">STRATEGY PARTNERS</span></div>
  <span class="nav-link" style="left:406px">CLIENTS</span>
  <span class="nav-link" style="left:457px">TESTIMONIALS</span>
  <span class="nav-link" style="left:525px">CONTACT US</span>
  <div class="search">
    <svg width="9" height="9" viewBox="0 0 10 10"><circle cx="4" cy="4" r="3" fill="none" stroke="#fff" stroke-width="1.4"/><line x1="6.2" y1="6.2" x2="9" y2="9" stroke="#fff" stroke-width="1.6"/></svg>SEARCH
  </div>
</header>

<section class="hero" role="img" aria-label="Lighthouse on a rocky shore under a starry violet and pink evening sky"></section>
<svg class="abs" style="left:0;top:180px" width="38" height="44"><polygon points="0,0 38,22 0,44" fill="var(--red)"/><polyline points="14,16 9,22 14,28" fill="none" stroke="#fff" stroke-width="2"/></svg>
<svg class="abs" style="left:667px;top:180px" width="38" height="44"><polygon points="38,0 0,22 38,44" fill="var(--red)"/><polyline points="24,16 29,22 24,28" fill="none" stroke="#fff" stroke-width="2"/></svg>
<div class="hero-title">NORTHVALE STRATEGY PARTNERS</div>

<h2 class="section-title" style="top:367px">WHAT WE OFFER</h2>

<svg class="abs" style="left:122px;top:418px" width="92" height="79" viewBox="0 0 92 79">
  <polygon points="46,0 92,79 0,79" fill="#ececec"/>
  <circle cx="46" cy="50" r="9" fill="none" stroke="var(--red)" stroke-width="1.6"/>
  <text x="46" y="54" text-anchor="middle" font-size="11" font-family="Asap,sans-serif" fill="var(--red)">$</text>
</svg>
<svg class="abs" style="left:306px;top:418px" width="92" height="79" viewBox="0 0 92 79">
  <polygon points="46,0 92,79 0,79" fill="#ececec"/>
  <polyline points="38,50 46,42 54,50" fill="none" stroke="var(--red)" stroke-width="1.6"/>
  <rect x="40" y="49" width="12" height="8" fill="none" stroke="var(--red)" stroke-width="1.6"/>
  <path d="M33 56 q6 8 14 6 l10 -4" fill="none" stroke="var(--red)" stroke-width="1.6"/>
</svg>
<svg class="abs" style="left:489px;top:418px" width="92" height="79" viewBox="0 0 92 79">
  <polygon points="46,0 92,79 0,79" fill="#ececec"/>
  <rect x="39" y="39" width="13" height="18" fill="none" stroke="var(--red)" stroke-width="1.6"/>
  <line x1="42" y1="44" x2="49" y2="44" stroke="var(--red)" stroke-width="1.2"/>
  <line x1="42" y1="48" x2="48" y2="48" stroke="var(--red)" stroke-width="1.2"/>
  <circle cx="53" cy="56" r="4.5" fill="#ececec" stroke="var(--red)" stroke-width="1.4"/>
</svg>

<div class="offer-name" style="left:78px">FINANCIAL ACCOUNTING</div>
<div class="offer-name" style="left:262px">PROPERTY PROTECTION</div>
<div class="offer-name" style="left:445px">TAX AND REGULATORY</div>
<p class="offer-text" style="left:77px">Lorem Ipsum is simply dummy text of the printing and typesetting industry. Lorem Ipsum has been the industry's standard dummy text ever</p>
<p class="offer-text" style="left:262px">Lorem Ipsum is simply dummy text of the printing and typesetting industry. Lorem Ipsum has been the industry's standard dummy text ever</p>
<p class="offer-text" style="left:445px">Lorem Ipsum is simply dummy text of the printing and typesetting industry. Lorem Ipsum has been the industry's standard dummy text ever</p>

<section class="provide"></section>
<h2 class="section-title" style="top:625px">WHAT WE PROVIDE ?</h2>

<svg class="abs" style="left:80px;top:670px" width="545" height="165" viewBox="80 670 545 165">
  <polygon points="174,675 347,675 258,825" fill="#9a9a9a" role="img" aria-label="Black and white photo of an audience at a business conference"/>
  <polygon points="174,675 258,825 85,825" fill="var(--navy)"/>
  <polygon points="442,678 618,678 530,828" fill="#a3a3a3" role="img" aria-label="Black and white portrait of a smiling executive in a suit"/>
  <polygon points="442,678 530,828 355,828" fill="var(--red)"/>
  <line x1="348" y1="747" x2="356" y2="747" stroke="#777" stroke-width="1.4"/>
  <line x1="352" y1="743" x2="352" y2="751" stroke="#777" stroke-width="1.4"/>
  <g font-family="Asap,sans-serif" font-size="14.5" fill="#fff" text-anchor="middle">
    <text x="170" y="778">CONSULTATIVE</text>
    <text x="170" y="795">SERVICES TO</text>
    <text x="170" y="812">BUSINESS C-SUITES</text>
    <text x="442" y="780">PERSONAL</text>
    <text x="442" y="797">COACHING TO</text>
    <text x="442" y="814">EXECUTIVES.</text>
  </g>
</svg>
<p class="provide-text" style="left:85px">Lorem Ipsum is simply dummy text of the printing and typesetting industry. Lorem Ipsum has been the industry's standard dummy text ever since the 1500s, when an unknown printer took a galley of type and scrambled</p>
<p class="provide-text" style="left:353px">Lorem Ipsum is simply dummy text of the printing and typesetting industry. Lorem Ipsum has been the industry's standard dummy text ever since the 1500s, when an unknown printer took a galley of type and scrambled</p>

<section class="newsletter"></section>
<svg class="abs" style="left:102px;top:934px" width="17" height="13" viewBox="0 0 17 13"><rect x="0.8" y="0.8" width="15.4" height="11.4" fill="none" stroke="var(--red)" stroke-width="1.4"/><polyline points="1,1 8.5,7 16,1" fill="none" stroke="var(--red)" stroke-width="1.4"/></svg>
<div class="news-label">NEWSLETTER SIGN UP</div>
<div class="email-field">ENTER YOUR E-MAIL ADDRESS</div>
<div class="subscribe">SUBSCRIBE NOW</div>

<div class="footer-rule" style="top:1003px"></div>
<div class="footer-brand"><span class="brand-name">NORTHVALE</span><span class="brand-sub">STRATEGY PARTNERS</span></div>

<div class="col-head h1" style="left:85px">QUICK LINKS</div>
<div class="col-head h2" style="left:175px">ABOUT US</div>
<div class="col-head h3" style="left:313px">NEWS</div>
<div class="col-head h4" style="left:450px">CONTACT US</div>

<ul class="quick"><li>Home</li><li>About Us</li><li>Services</li><li>Clients</li><li>Testimonials</li><li>Contact Us</li></ul>
<p class="small" style="left:175px;top:1069px;width:125px">Lorem Ipsum is simply dummy text of the printing and typesetting industry. Lorem Ipsum has been the industry's standard dummy text ever since the 1500s</p>
<p class="small" style="left:313px;top:1069px;width:115px"><span class="date">December 30th, 2015</span><br><span style="display:block;margin-top:3px">Lorem Ipsum is simply dummy text of the printing and typesetting industry.</span></p>
<p class="small" style="left:313px;top:1113px;width:115px"><span class="date">December 30th, 2015</span><br><span style="display:block;margin-top:3px">Lorem Ipsum is simply dummy text of the printing and typesetting industry.</span></p>

<svg class="ico" style="top:1070px" width="8" height="8" viewBox="0 0 8 8"><polygon points="4,0 8,2 0,2" fill="var(--red)"/><rect x="1" y="3" width="1.2" height="3.5" fill="var(--red)"/><rect x="3.4" y="3" width="1.2" height="3.5" fill="var(--red)"/><rect x="5.8" y="3" width="1.2" height="3.5" fill="var(--red)"/><rect x="0" y="7" width="8" height="1" fill="var(--red)"/></svg>
<p class="small" style="left:470px;top:1069px">Northvale Office<br>Lindenweg 42<br>10117 Berlin | Germany</p>
<svg class="ico" style="top:1110px" width="7" height="7" viewBox="0 0 7 7"><path d="M1 0 L2.6 0 L3 2 L2 2.8 Q3 4.5 4.2 5 L5 4 L7 4.4 L7 6 Q7 7 6 7 Q0 6 0 1 Q0 0 1 0Z" fill="var(--red)"/></svg>
<p class="small" style="left:470px;top:1109px">Telephone: +49 30 5550 1824</p>
<svg class="ico" style="top:1130px" width="8" height="6" viewBox="0 0 8 6"><rect x=".5" y=".5" width="7" height="5" fill="none" stroke="var(--red)"/><polyline points=".5,.5 4,3.5 7.5,.5" fill="none" stroke="var(--red)"/></svg>
<p class="small" style="left:470px;top:1128px">E-mail: hello@northvale-partners.de</p>

<div class="footer-rule" style="top:1166px"></div>
<p class="copy" style="left:85px">© 2015 Company Name | All Rights Reserved</p>
<p class="copy" style="left:525px">Connect With Us</p>
<svg class="abs" style="left:572px;top:1179px" width="50" height="6"><g fill="#555"><rect x="0" y="0" width="6" height="6"/><rect x="11" y="0" width="6" height="6"/><rect x="22" y="0" width="6" height="6"/><rect x="33" y="0" width="6" height="6"/><rect x="44" y="0" width="6" height="6"/></g></svg>

</body>
</html>
```